Internal Office Slogans / Motto / Vision Statements

Hi. We would like to put up some posters around the office with quotations such as -
-”Do what you do so well that they will want to see it again and bring their friends.”- Hollis Brandt
-Make your customers feel heard and understood. Make your customers feel respected and liked. Make your customers feel appreciated and helped. Understand that you can do none of these things unless you are sincere about them.
Terrence Oakley
- It’s a very predictable and satisfying phenomenon: whenever we get better, our customers do too.
Cal Pruett
-Catch people in the act of performing extraordinary customer service. Treat them like heroes. Tell their stories, far and wide.
Ned Farraday

The purpose of the posters is to reiterate our culture and vision within the organisation. They should be clean, crisp and eye catching, not gaudy or bright. Professional, bold and strong.

The company website and logo is at http://www.nexoraweb.com.au
Print size will be A1

Thanks for participating & looking forward to seeing your great work.
Updates

Hi All. . 

So to reiterate we are looking for one background design to be used for multiple quotes...  The list of quotes are as follows: 

Support and or Sales Office

 

Make your customers feel heard and understood.Make your customers feel respected and liked. Make your customers feelappreciated and helped. Understand that you can do none of these things unlessyou are sincere about them.

Terrence Oakley

 

Nothing liberates our greatness like the desireto help, the desire to serve

Dorothea Quill

 

It’s a very predictable and satisfying phenomenon:whenever we get better, our customers do too.

Cal Pruett

 

Success means we go to sleep at night knowingthat our talents and abilities were used in a way that served others.

Dorothea Quill.

 

The sole purpose of business is to create, serveand satisfy a customer, from beginning to end – and that’s everyone’s job.

Ned Farraday

 

We don’t celebrate closing a sale, we celebrateopening a relationship.

Rosalind Hext

I will never make you a promise – unless I giveyou a plan and procedure to make that promise possible.

Bo Tennant

 

Customers feel we take them for granted; onlyshow interest when we want an order; lavish our time on prospects; communicatemainly by invoice; are fixated on big accounts; drop them like hot potatoesonce we have the order; don’t follow through on promises; and satisfy our ownbureaucracy rather than their needs. We can do better than that, much better.

Alan P Merrow.

 

 

General and public area

 

Catch people in the act of performingextraordinary customer service. Treat them like heroes. Tell their stories, farand wide.

Ned Farraday

 

 

We see our customers as invited guests to aparty, and we are the hosts. It’s our job every day to make every importantaspect of the customer experience a little bit better." Carl Voight - Founder andCEO of Halverin

 

"If you do build a great experience,customers tell each other about that. Word of mouth is verypowerful."  Carl Voight

 

It's not a faithin technology. It's faith in people. Rick Palmer

 

“Being the richest man in the cemetery doesn’tmatter to me … Going to bed at night saying we’ve done something wonderful…that’s what matters to me.” Rick Palmer

 

The customer experience is the next competitivebattleground. Lance Morrow, CIO, Vantor Computers

 

”Do what you do so well that they will want tosee it again and bring their friends.”- Hollis Brandt

In the world of internet customer service, it isimportant to remember your competitor is only a mouse click away. FrankHolden (not sure who he is but like the quote).

The customer is why you go to work. If they goaway, you do, too. Peter Lindqvist (?)

 

MaybeSome for Sales or Build Team:

Quality is remembered long after the price is forgotten. Marzetti Family Slogan

```html
<!DOCTYPE html>
<html lang="en">
<head>
<meta charset="utf-8">
<title>Customer Service Quote Poster</title>
<link href="https://fonts.googleapis.com/css2?family=Anton&family=Poppins:wght@600&display=swap" rel="stylesheet">
<style>
  :root {
    --paper-light: #efe0bd;
    --paper-mid: #e3cc9c;
    --paper-dark: #c9a56b;
    --rule-blue: rgba(92, 150, 160, 0.45);
    --ink: #0f0c0a;
    --frame-ink: #3b3937;
    --hole: #0a0a0a;
    --accent: #c4461c;
  }
  html, body {
    margin: 0;
    padding: 0;
    width: 848px;
    height: 1200px;
    overflow: hidden;
  }
  .poster {
    position: relative;
    width: 848px;
    height: 1200px;
    overflow: hidden;
    background:
      radial-gradient(ellipse at 85% 45%, rgba(170, 110, 50, 0.35), transparent 40%),
      radial-gradient(ellipse at 10% 90%, rgba(160, 110, 60, 0.3), transparent 45%),
      radial-gradient(ellipse at 50% 40%, var(--paper-light), var(--paper-mid) 70%, var(--paper-dark));
  }
  .ruled-lines {
    position: absolute;
    inset: 0;
    background: repeating-linear-gradient(
      to bottom,
      transparent 0,
      transparent 20px,
      var(--rule-blue) 20px,
      var(--rule-blue) 21px
    );
  }
  .punch-hole {
    position: absolute;
    left: 11px;
    width: 23px;
    height: 23px;
    border-radius: 50%;
    background: var(--hole);
  }
  .frame {
    position: absolute;
    inset: 0;
  }
  .quote {
    position: absolute;
    left: 126px;
    top: 255px;
    width: 620px;
    margin: 0;
    font-family: "Anton", "Impact", sans-serif;
    font-size: 44px;
    line-height: 62.6px;
    letter-spacing: 2px;
    color: var(--ink);
    text-align: center;
  }
  .author {
    position: absolute;
    left: 434px;
    top: 984px;
    margin: 0;
    font-family: "Poppins", "Arial", sans-serif;
    font-weight: 600;
    font-size: 26px;
    line-height: 1;
    letter-spacing: 0.8px;
    white-space: nowrap;
    color: var(--accent);
    transform: rotate(9deg);
    transform-origin: left top;
  }
</style>
</head>
<body>
<main class="poster">
  <div class="ruled-lines"></div>

  <span class="punch-hole" style="top:96px"></span>
  <span class="punch-hole" style="top:424px"></span>
  <span class="punch-hole" style="top:754px"></span>
  <span class="punch-hole" style="top:1082px"></span>

  <svg class="frame" width="848" height="1200" viewBox="0 0 848 1200" aria-hidden="true">
    <g fill="none" stroke="var(--frame-ink)" stroke-linecap="round">
      <path d="M158 118 L832 234" stroke-width="6"/>
      <path d="M165 128 L826 242" stroke-width="3"/>
      <path d="M160 114 L500 170" stroke-width="2"/>
      <path d="M829 230 L690 1062" stroke-width="6"/>
      <path d="M820 244 L698 1050" stroke-width="2.5"/>
      <path d="M688 1062 L18 966" stroke-width="6"/>
      <path d="M680 1052 L26 958" stroke-width="2.5"/>
      <path d="M18 968 L162 116" stroke-width="6"/>
      <path d="M30 955 L170 128" stroke-width="2.5"/>
    </g>
  </svg>

  <p class="quote">
    Make your customers feel<br>
    heard and<br>
    understood.Make your<br>
    customers feel respected<br>
    and liked. Make your<br>
    customers feel<br>
    appreciated and helped.<br>
    Understand that you can<br>
    do none of these things<br>
    unlessyou are sincere<br>
    about them.
  </p>

  <p class="author">Terrence Oakley</p>
</main>
</body>
</html>
```